Australian Trucking Company Requires Professional Looking Stationary

We require a professional looking stationary design that incorporates our newly designed logo.

Our business, called "Brell Haulage Contracting", provides contracting work, transport and logistics to business in Western Australia particularly with links to the mining sector.

We are a small business looking to expand and our new logo and our new stationary will help develop our brand image in our market place.

Target Market(s)

Businesses and Corporation with links to the Mining Sector

Industry/Entity Type

Small Business

Requirements
Must have
• The letterhead must have the following details:
The new logo

Text saying: "Brell Holdings Pty Ltd (ACN 582 316 907) ATF The Brell Discretionary Trust T/AS"
"ABN 71 834 209 553"
Address "P.O Box 817 Wattlegrove WA, 6958"
Phone: 08 9352 7140
Email: brellhaul@mailbox-example.com.au

The text on the letterhead should be editable as the details are likely to change in the near future. Provision should be made for a website address all though one isn't available at the moment.

The styling, layout and font text is entirely up to the designer.

```html
<!DOCTYPE html>
<html lang="en">
<head>
<meta charset="utf-8">
<title>Brell Haulage Contracting – Business Card</title>
<link href="https://fonts.googleapis.com/css2?family=Open+Sans:wght@400;600;700;800&display=swap" rel="stylesheet">
<style>
  :root {
    --backdrop: #7b4a2b;
    --card-white: #f4f4f4;
    --brand-red: #c8101f;
    --deep-red: #8e0a14;
    --ink: #3a3a3a;
    --ink-soft: #555555;
    --rule-grey: #8c8c8c;
    --paper: #ffffff;
  }
  * { margin: 0; padding: 0; box-sizing: border-box; }
  html, body {
    width: 1200px; height: 426px; overflow: hidden;
    background: var(--backdrop);
    font-family: "Open Sans", Arial, sans-serif;
  }
  .canvas { position: relative; width: 1200px; height: 426px; }

  .card {
    position: absolute; top: 57px; width: 522px; height: 295px;
    border-radius: 18px; overflow: hidden;
    box-shadow: 0 4px 10px rgba(0,0,0,0.35);
  }
  .card--front { left: 68px; background: var(--card-white); }
  .card--back {
    left: 610px;
    background: radial-gradient(ellipse at 55% 45%, #e3222f 0%, var(--brand-red) 40%, var(--deep-red) 100%);
  }

  .brand-name {
    position: absolute; left: 32px; top: 30px;
    color: var(--brand-red); font-weight: 800;
    font-size: 31px; line-height: 31px; letter-spacing: 0.5px;
    text-transform: uppercase;
  }

  .contact-list { position: absolute; left: 22px; top: 160px; font-size: 12px; color: var(--ink); }
  .contact-row { display: flex; align-items: center; gap: 4px; height: 13px; margin-bottom: 0; white-space: nowrap; }
  .contact-row + .contact-row { margin-top: 0; }
  .contact-row--pair { gap: 4px; }
  .contact-row--pair .gap { width: 8px; }
  .contact-row--address { margin-top: 12px; }
  .icon { width: 10px; height: 10px; flex: none; }

  .person { position: absolute; left: 25px; top: 220px; color: var(--ink); white-space: nowrap; }
  .person-name { font-size: 17px; font-weight: 700; }
  .person-role { font-size: 12px; color: var(--ink-soft); }

  .swoosh { position: absolute; left: 0; top: 0; width: 522px; height: 295px; }

  .legal {
    position: absolute; right: 22px; top: 209px;
    text-align: right; color: var(--paper);
    font-size: 11.5px; line-height: 16.5px;
  }

  .back-name {
    position: absolute; left: 0; right: 0; top: 112px;
    text-align: center; color: var(--paper);
    font-weight: 800; font-size: 30px; line-height: 34px;
    text-transform: uppercase; letter-spacing: 1px;
  }
</style>
</head>
<body>
<div class="canvas">

  <section class="card card--front">
    <svg class="swoosh" viewBox="0 0 522 295" aria-hidden="true">
      <defs>
        <linearGradient id="swooshRed" x1="0" y1="1" x2="1" y2="0">
          <stop offset="0" stop-color="#a50c18"/>
          <stop offset="0.6" stop-color="#d41424"/>
          <stop offset="1" stop-color="#b00d1a"/>
        </linearGradient>
      </defs>
      <path d="M0 252 L250 252 L250 258 L0 258 Z" fill="var(--rule-grey)"/>
      <path d="M82 252 L165 252 L165 258 L82 258 Z" fill="var(--brand-red)"/>
      <path d="M215 295 C260 230 320 175 410 150 C455 138 495 140 522 145 L522 295 Z" fill="#e8e8e8"/>
      <path d="M222 295 C268 236 330 184 415 160 C458 148 495 150 522 155 L522 295 Z" fill="url(#swooshRed)"/>
    </svg>

    <div class="brand-name">Brell<br>Haulage<br>Contracting</div>

    <div class="contact-list">
      <div class="contact-row">
        <svg class="icon" viewBox="0 0 10 10" aria-hidden="true"><path d="M2 0.5 L3.8 2.6 L2.8 3.6 C3.4 5 4.8 6.4 6.3 7.1 L7.3 6.1 L9.5 8 L8 9.5 C4.5 9 1 5.5 0.5 2 Z" fill="var(--brand-red)"/></svg>
        <span>08 9352 7140</span>
      </div>
      <div class="contact-row contact-row--pair">
        <svg class="icon" viewBox="0 0 10 10" aria-hidden="true"><rect x="0.5" y="2" width="9" height="6" fill="none" stroke="var(--brand-red)" stroke-width="1.2"/><path d="M0.5 2 L5 5.5 L9.5 2" fill="none" stroke="var(--brand-red)" stroke-width="1.2"/></svg>
        <span>brellhaul@mailbox-example.com.au</span>
        <span class="gap"></span>
        <svg class="icon" viewBox="0 0 10 10" aria-hidden="true"><circle cx="5" cy="5" r="4.3" fill="none" stroke="var(--brand-red)" stroke-width="1.1"/><ellipse cx="5" cy="5" rx="1.8" ry="4.3" fill="none" stroke="var(--brand-red)" stroke-width="0.9"/><path d="M0.7 5 H9.3" stroke="var(--brand-red)" stroke-width="0.9"/></svg>
        <span>www.brellhaulsite.com</span>
      </div>
      <div class="contact-row contact-row--address">
        <svg class="icon" viewBox="0 0 10 10" aria-hidden="true"><path d="M5 0.5 L9.5 5 L8 5 L8 9.5 L6 9.5 L6 6.5 L4 6.5 L4 9.5 L2 9.5 L2 5 L0.5 5 Z" fill="var(--brand-red)"/></svg>
        <span>P.O Box 817 Wattlegrove WA, 6958</span>
      </div>
    </div>

    <div class="person">
      <span class="person-name">Persons name,</span>
      <span class="person-role">Manager</span>
    </div>

    <div class="legal">
      <p>Brell Holdings Pty Ltd (ACN 582 316 907)</p>
      <p>ATF The Brell Discretionary Trust T/AS</p>
      <p>ABN 71 834 209 553</p>
    </div>
  </section>

  <section class="card card--back">
    <div class="back-name">Brell<br>Haulage<br>Contracting</div>
  </section>

</div>
</body>
</html>
```